Business Card Design needed - Something Awesome!

Need a business card designed. Company is "Marlowe Advisory" we do consulting and also have sales automation technology.
I'm going to use thick stock or metal, something really nice... I was thinking about a QR Code on the back that would just upload my contact info to the persons contact, etc -

This is a Strategy Company with a tech feel. I'm open to ideas but really want this to be nice!

I need a template that should include:

Name | Position or Title
D: 415.902.3376
www.marloweadvisory.example

I'm going to attach my contact so you can use that one, I need to get this printed.

Target Market(s)

Small to mid size customers, Entrepreneurs etc.

Industry/Entity Type

Consulting, Tech, Private Equity.

Contact Information for Business Card

Name, Phone, Maybe email, URL

Font styles to use
Sans Serif

Colors

Designer to choose only greyscale colors for use in the design.

Requirements
Must have
• Fresh, Clean, stand out from the crowd - will be on thick stock or metal.
Nice to have
• Clean, simple yet impactful.
Should not have
• Not cartoonish

```html
<!DOCTYPE html>
<html lang="en">
<head>
<meta charset="utf-8">
<title>Marlowe Advisory — Business Card</title>
<link href="https://fonts.googleapis.com/css2?family=Roboto:wght@300;400;700&display=swap" rel="stylesheet">
<style>
  :root {
    --backdrop: #2f2f2f;
    --card: #111111;
    --card-edge: #1c1c1c;
    --silver: #c9c9c9;
    --silver-soft: #9a9a9a;
    --silver-dim: #6f6f6f;
    --rule: #8a8a8a;
  }
  * { margin: 0; padding: 0; box-sizing: border-box; }
  html, body { width: 1200px; height: 801px; overflow: hidden; }
  body {
    background: var(--backdrop);
    font-family: "Roboto", Arial, sans-serif;
    position: relative;
  }
  .card {
    position: absolute;
    top: 250px;
    width: 520px;
    height: 300px;
    background: var(--card);
    border: 1px solid var(--card-edge);
    box-shadow: 0 18px 40px rgba(0,0,0,.45);
    overflow: hidden;
  }
  .card--front { left: 50px; }
  .card--back { left: 630px; }

  .wordmark {
    position: absolute;
    top: 40px;
    right: 40px;
    font-weight: 300;
    font-size: 30px;
    letter-spacing: 3px;
    color: var(--silver);
    text-transform: uppercase;
  }
  .main-rule {
    position: absolute;
    top: 118px;
    left: 40px;
    right: 40px;
    height: 1px;
    background: var(--rule);
  }
  .identity {
    position: absolute;
    left: 40px;
    top: 150px;
  }
  .identity__name {
    font-weight: 700;
    font-size: 17px;
    letter-spacing: .5px;
    color: var(--silver);
    text-transform: uppercase;
  }
  .identity__title {
    margin-top: 4px;
    font-weight: 400;
    font-size: 13px;
    color: var(--silver-dim);
  }
  .identity__rule {
    width: 150px;
    height: 1px;
    background: var(--silver-dim);
    margin: 14px 0 12px;
  }
  .contact {
    list-style: none;
    font-size: 13px;
    color: var(--silver-soft);
    line-height: 20px;
  }
  .contact li { display: flex; align-items: center; gap: 7px; }
  .contact svg { width: 10px; height: 10px; fill: var(--silver); }
  .web {
    position: absolute;
    right: 40px;
    bottom: 30px;
    text-align: right;
  }
  .web__url {
    font-size: 13px;
    color: var(--silver-soft);
  }
  .web__bar {
    margin-top: 8px;
    margin-left: auto;
    width: 170px;
    height: 9px;
    background: linear-gradient(90deg, #5c5c5c, #e8e8e8 45%, #8d8d8d);
  }

  .back-mark {
    position: absolute;
    inset: 0;
    display: flex;
    align-items: center;
    justify-content: center;
    gap: 14px;
  }
  .back-mark__square {
    width: 22px;
    height: 22px;
    background: var(--silver-soft);
  }
  .back-mark__name {
    font-weight: 300;
    font-size: 24px;
    letter-spacing: 3px;
    color: var(--silver);
    text-transform: uppercase;
  }
</style>
</head>
<body>
  <section class="card card--front">
    <div class="wordmark">Marlowe Advisory</div>
    <div class="main-rule"></div>
    <div class="identity">
      <div class="identity__name">Julian R. Ashford</div>
      <div class="identity__title">Founder / CEO</div>
      <div class="identity__rule"></div>
      <ul class="contact">
        <li>
          <svg viewBox="0 0 10 10" aria-hidden="true"><path d="M2 0.5 L3.8 0.5 L4.4 3 L3.2 3.9 C3.8 5.2 4.8 6.2 6.1 6.8 L7 5.6 L9.5 6.2 L9.5 8 C9.5 9 8.8 9.5 8 9.5 C4 9.3 0.7 6 0.5 2 C0.5 1.2 1 0.5 2 0.5 Z"/></svg>
          415.902.3376
        </li>
        <li>
          <svg viewBox="0 0 10 10" aria-hidden="true"><path d="M0.5 2 L9.5 2 L9.5 8.5 L0.5 8.5 Z M1 2.4 L5 5.6 L9 2.4" stroke="#111" stroke-width=".8"/></svg>
          info@marloweadvisory.example
        </li>
      </ul>
    </div>
    <div class="web">
      <div class="web__url">www.marloweadvisory.example</div>
      <div class="web__bar"></div>
    </div>
  </section>

  <section class="card card--back">
    <div class="back-mark">
      <span class="back-mark__square"></span>
      <span class="back-mark__name">Marlowe Advisory</span>
    </div>
  </section>
</body>
</html>
```